Bork Ventures, Inc. Website redesign

Revamp the website, it is old and outdated. www.borkventuresinc.example

Target Market(s)

Information Technology Consulting and Staffing

Coding

Coded - Design and coding required

Number of Pages Required

5+ page

Colors

Designer to choose colors to be used in the design.

Requirements
Must have
• Outlined text boxes just like from the Tolvane.example site. A clean look

```html
<!DOCTYPE html>
<html lang="en">
<head>
<meta charset="utf-8">
<title>Bork Ventures, Inc. | Mission Integrity Results</title>
<link href="https://fonts.googleapis.com/css2?family=Varela+Round&family=Lato:wght@400;700&display=swap" rel="stylesheet">
<style>
:root{
  --red:#a01a2f;
  --red-light:#b8364a;
  --pink:#ecd0d6;
  --ink:#1d1d1f;
  --grey:#7a7a7a;
  --line:#e3e3e3;
  --dark:#1b1b1d;
  --white:#ffffff;
}
*{box-sizing:border-box;margin:0;padding:0}
html,body{width:1200px;height:4005px;overflow:hidden}
body{position:relative;background:var(--white);font-family:"Lato",sans-serif;color:var(--ink)}
.abs{position:absolute}
.heading{font-family:"Varela Round",sans-serif;font-weight:400}
.btn{position:absolute;display:flex;align-items:center;justify-content:center;border:1.5px solid var(--red);color:var(--red);font-size:15px;background:var(--white)}
.btn--light{border-color:var(--white);color:var(--white);background:transparent}
.mark{width:16px;height:16px;background:var(--red);border-radius:3px;position:absolute}
.mark--light{background:var(--white)}

/* header */
.site-header{top:0;left:0;width:1200px;height:67px;background:var(--white)}
.brand{left:162px;top:16px;display:flex;align-items:center;gap:10px}
.brand__name{font-family:"Varela Round",sans-serif;font-size:22px;color:var(--ink);letter-spacing:1px}
.brand__box{width:26px;height:26px;background:var(--red);border-radius:4px}
.brand__tag{font-family:"Varela Round",sans-serif;font-size:18px;color:#555;margin-left:8px}
.nav{top:25px;left:609px;display:flex;gap:28px;font-size:12px;font-weight:700}
.nav a{color:var(--ink);text-decoration:none}
.nav a.is-active{color:var(--red);border-bottom:1.5px solid var(--red);padding-bottom:3px}

/* hero */
.hero-bg{top:67px;left:0}
.hero__eyebrow{top:136px;width:1200px;text-align:center;font-size:25px;color:var(--ink)}
.hero__title{top:178px;width:1200px;text-align:center;font-size:50px;color:var(--white)}
.hero__text{top:250px;left:305px;width:590px;text-align:center;font-size:12.5px;line-height:21px;color:var(--white)}
.hero__photo{left:162px;top:446px;width:876px;height:336px;border-radius:8px;background:linear-gradient(120deg,#8f9aa6 0%,#e8ecf0 40%,#c9d2da 70%,#7fb0c6 100%)}

/* sections */
.section-title{width:1200px;text-align:center;font-size:50px;color:var(--ink)}

/* services */
.service{top:956px;width:202px;height:284px;border:1px solid var(--line);border-radius:4px;background:var(--white);text-align:center}
.service--active{background:var(--red);border-color:var(--red)}
.service__icon{position:absolute;left:66px;top:24px}
.service__title{position:absolute;top:115px;width:100%;font-size:13px;font-weight:700}
.service__text{position:absolute;top:136px;left:14px;width:174px;font-size:11px;line-height:19.5px;color:var(--grey)}
.service--active .service__title{color:#f0c9d0}
.service--active .service__text{color:var(--white)}
.service .btn{left:44px;top:218px;width:114px;height:36px}

/* about */
.about__title{left:162px;top:1412px;font-size:50px;color:var(--white)}
.about__text{left:162px;top:1494px;width:424px;font-size:11.5px;line-height:21px;color:var(--white)}
.about__photo{left:611px;top:1416px;width:427px;height:412px;border-radius:6px;background:radial-gradient(circle at 55% 45%,#5fb5b0 0%,#2f6f70 35%,#1a2a2c 75%)}

/* strategy */
.strategy__photo{left:359px;top:2075px;width:482px;height:482px;border-radius:50%;background:radial-gradient(circle at 50% 50%,#f3f4f7 0%,#e6e9ef 55%,#d6dbe4 100%)}
.strategy__title{top:2195px;width:1200px;text-align:center;font-size:48px}
.strategy__text{top:2276px;left:425px;width:350px;text-align:center;font-size:11px;line-height:19.5px;color:#888}
.strategy__link{top:2402px;width:1200px;text-align:center;font-size:14px;color:var(--red)}
.strategy__link span{border-bottom:1.5px solid var(--red);padding-bottom:2px}
.step-label{font-size:12.5px;font-weight:700}

/* news */
.news{top:2801px;height:314px;background:var(--white);box-shadow:0 2px 10px rgba(0,0,0,.1)}
.news--active{border-bottom:3px solid var(--red)}
.news__photo{position:absolute;left:0;top:0;width:233px;height:187px}
.news__date{position:absolute;right:4px;top:40px;writing-mode:vertical-rl;transform:rotate(180deg);font-size:10px;color:#999}
.news__title{position:absolute;left:13px;top:198px;font-size:12.5px;font-weight:700}
.news--active .news__title{color:var(--red)}
.news__text{position:absolute;left:13px;top:220px;width:218px;font-size:11px;line-height:19.5px;color:var(--grey)}
.news__more{position:absolute;right:10px;top:218px;width:28px;height:80px;border:1px solid #bbb;display:flex;align-items:center;justify-content:center}
.news__more span{writing-mode:vertical-rl;transform:rotate(180deg);font-size:10px;color:#999}
.news--active .news__more{border-color:var(--red)}
.news--active .news__more span{color:var(--red)}

/* contact */
.field{border:1px solid #d8d8d8;border-radius:3px;font-size:11px;color:#777;padding:15px 12px}

/* footer */
.footer-bg{top:3560px;left:0}
.footer__brand{left:162px;top:3712px;display:flex;align-items:center;gap:10px}
.footer__brand .brand__name{color:var(--white)}
.footer__about{left:162px;top:3753px;width:200px;font-size:11px;line-height:20px;color:#d9d9d9}
.social{left:162px;top:3880px;display:flex;gap:13px}
.social span{width:32px;height:32px;border:1.5px solid var(--white);border-radius:50%}
.footer__col{top:3702px}
.footer__col h4{font-family:"Lato",sans-serif;font-weight:400;font-size:14px;color:#c8283f;margin-bottom:14px}
.footer__col li{list-style:none;font-size:11px;line-height:21px;color:#e2e2e2}
.contact-row{display:flex;align-items:flex-start;gap:16px;font-size:11px;line-height:21px;color:#e2e2e2;margin-bottom:22px}
.copyright{top:3959px;left:0;width:1200px;height:46px;background:var(--red);color:var(--white);font-size:11px;display:flex;align-items:center;justify-content:center}
</style>
</head>
<body>

<header class="abs site-header">
  <div class="abs brand"><span class="brand__box"></span><span class="brand__name">Bork Ventures</span><span class="brand__tag">Mission Integrity Results</span></div>
  <nav class="abs nav"><a href="#">Home</a><a href="#" class="is-active">About Us</a><a href="#">Services</a><a href="#">Strategy</a><a href="#">IT News</a><a href="#">Contact Us</a></nav>
</header>

<svg class="abs hero-bg" width="1200" height="640" viewBox="0 0 1200 640" aria-hidden="true">
  <polygon points="0,0 1200,0 1200,620 0,586" fill="var(--red)"/>
  <polygon points="1200,520 1200,632 800,600" fill="var(--red-light)"/>
</svg>

<section>
  <p class="abs hero__eyebrow heading">BORK VENTURES</p>
  <h1 class="abs hero__title heading">Mission Integrity Results</h1>
  <p class="abs hero__text">Bork Ventures, Inc. is an 8(a) full-service IT consulting company based in the Washington, DC Metro area. We offer specialized, highly customized technology solutions for our customers located throughout the United States.</p>
  <a class="btn btn--light" style="left:524px;top:343px;width:151px;height:52px;font-size:19px">Contact Us</a>
  <div class="abs hero__photo" role="img" aria-label="Photo of hands reviewing a printed report beside a laptop"></div>
</section>

<section>
  <span class="mark" style="left:592px;top:834px"></span>
  <h2 class="abs section-title heading" style="top:858px">Our Services</h2>

  <div class="abs service" style="left:162px">
    <svg class="service__icon" width="70" height="70" viewBox="0 0 70 70" aria-hidden="true"><circle cx="35" cy="35" r="33" fill="none" stroke="var(--red)" stroke-dasharray="3 3"/><circle cx="35" cy="35" r="26" fill="var(--red)"/><rect x="23" y="26" width="24" height="16" rx="1" fill="none" stroke="#fff" stroke-width="1.6"/><path d="M31 46h8M35 42v4" stroke="#fff" stroke-width="1.6"/></svg>
    <h3 class="service__title">Hardware / Software Sales</h3>
    <p class="service__text">We have access to multiple distributor partners throughout North America, as well as...</p>
    <a class="btn">Read More</a>
  </div>
  <div class="abs service service--active" style="left:387px">
    <svg class="service__icon" width="70" height="70" viewBox="0 0 70 70" aria-hidden="true"><circle cx="35" cy="35" r="33" fill="none" stroke="#fff" stroke-dasharray="3 3"/><circle cx="35" cy="35" r="26" fill="#fff"/><circle cx="35" cy="35" r="9" fill="none" stroke="var(--red)" stroke-width="1.6" stroke-dasharray="4 2"/><circle cx="35" cy="35" r="3" fill="var(--red)"/></svg>
    <h3 class="service__title">Professional Services</h3>
    <p class="service__text">Our team provides experienced leadership and guidance, utilizing the industry standard...</p>
    <a class="btn btn--light">Read More</a>
  </div>
  <div class="abs service" style="left:612px">
    <svg class="service__icon" width="70" height="70" viewBox="0 0 70 70" aria-hidden="true"><circle cx="35" cy="35" r="33" fill="none" stroke="var(--red)" stroke-dasharray="3 3"/><circle cx="35" cy="35" r="26" fill="var(--red)"/><g fill="none" stroke="#fff" stroke-width="1.5"><circle cx="35" cy="28" r="4"/><circle cx="26" cy="42" r="3.5"/><circle cx="35" cy="42" r="3.5"/><circle cx="44" cy="42" r="3.5"/><path d="M35 32v6M33 31l-6 8M37 31l6 8"/></g></svg>
    <h3 class="service__title">Technology Assessment</h3>
    <p class="service__text">xperience has shown companies that perform objective, third-party technology.</p>
    <a class="btn">Read More</a>
  </div>
  <div class="abs service" style="left:836px">
    <svg class="service__icon" width="70" height="70" viewBox="0 0 70 70" aria-hidden="true"><circle cx="35" cy="35" r="33" fill="none" stroke="var(--red)" stroke-dasharray="3 3"/><circle cx="35" cy="35" r="26" fill="var(--red)"/><g fill="none" stroke="#fff" stroke-width="1.5"><rect x="25" y="22" width="20" height="14"/><path d="M28 33l5-5 4 3 5-6"/><circle cx="27" cy="42" r="2.5"/><circle cx="35" cy="42" r="2.5"/><circle cx="43" cy="42" r="2.5"/><path d="M23 49a4 4 0 0 1 8 0M31 49a4 4 0 0 1 8 0M39 49a4 4 0 0 1 8 0"/></g></svg>
    <h3 class="service__title">Technology Consulting</h3>
    <p class="service__text">Implementing quality solutions is more than applying technology to problems...</p>
    <a class="btn">Read More</a>
  </div>
</section>

<svg class="abs" style="left:0;top:1330px" width="1200" height="620" viewBox="0 0 1200 620" aria-hidden="true">
  <polygon points="600,40 1200,0 1200,45" fill="var(--pink)"/>
  <polygon points="0,540 1200,535 1200,575 0,608" fill="var(--pink)"/>
  <polygon points="0,7 1200,45 1200,535 0,543" fill="var(--red)"/>
</svg>

<section>
  <span class="mark mark--light" style="left:162px;top:1392px"></span>
  <h2 class="abs about__title heading">About Us</h2>
  <div class="abs about__text">
    <p>Bork Ventures, Inc. is an 8(a) innovative and rapidly growing full-service IT consulting firm. We provide our clients with cutting-edge technologies and the know-how to apply them to their individual business models.</p>
    <p>For over 20+ years, we have been providing reliable IT solutions to businesses in the Washington, DC Metro area and beyond. Our comprehensive services provide clients with unique technology solutions that are customized to meet the specific demands of their business.</p>
    <p>Look to our experts for strategic IT guidance, management and services that allows you to take your mind off technology and concentrate on your core area of business. Bork Ventures, Inc. provides cost-efficient solutions that simply make good sense.</p>
  </div>
  <a class="btn btn--light" style="left:162px;top:1777px;width:112px;height:37px">Read More</a>
  <div class="abs about__photo" role="img" aria-label="Close-up photo of fibre optic network cables plugged into a switch"></div>
</section>

<section>
  <div class="abs strategy__photo" role="img" aria-label="Faded photo of a business meeting behind the strategy text"></div>
  <svg class="abs" style="left:0;top:2000px" width="1200" height="600" viewBox="0 0 1200 600" aria-hidden="true">
    <circle cx="600" cy="316" r="243" fill="none" stroke="var(--red)" stroke-width="1.3" stroke-dasharray="5 4"/>
    <g fill="#fff" stroke="var(--red)" stroke-width="1.3">
      <circle cx="603" cy="80" r="40" stroke-dasharray="3 3"/><circle cx="603" cy="80" r="32"/>
      <circle cx="367" cy="238" r="40" stroke-dasharray="3 3"/><circle cx="367" cy="238" r="32"/>
      <circle cx="441" cy="500" r="40" stroke-dasharray="3 3"/><circle cx="441" cy="500" r="32"/>
      <circle cx="768" cy="489" r="40" stroke-dasharray="3 3"/><circle cx="768" cy="489" r="32"/>
      <circle cx="832" cy="234" r="52" stroke-width="3"/>
    </g>
    <circle cx="832" cy="234" r="40" fill="var(--red)"/>
    <g fill="none" stroke="var(--red)" stroke-width="1.5">
      <circle cx="600" cy="77" r="11"/><path d="M608 85l9 9"/>
      <rect x="354" y="226" width="26" height="22"/><path d="M358 242l6-6 5 4 7-8"/>
      <rect x="428" y="489" width="26" height="22"/><path d="M433 506v-6M439 506v-10M445 506v-8"/>
      <rect x="754" y="476" width="28" height="18"/><path d="M768 494v6M760 502h16"/>
    </g>
    <g fill="none" stroke="#fff" stroke-width="1.8"><circle cx="832" cy="234" r="14" stroke-dasharray="5 3"/><circle cx="832" cy="234" r="5"/></g>
  </svg>
  <span class="abs step-label" style="left:579px;top:2006px">Assess</span>
  <span class="abs step-label" style="left:232px;top:2231px">Recommend</span>
  <span class="abs" style="left:896px;top:2224px;font-size:17px;color:var(--red)">Manage</span>
  <span class="abs step-label" style="left:406px;top:2556px">Implement</span>
  <span class="abs step-label" style="left:750px;top:2548px">Monitor</span>
  <span class="mark" style="left:592px;top:2174px"></span>
  <h2 class="abs strategy__title heading">Our Strategy</h2>
  <p class="abs strategy__text">Civilian and Federal agencies are facing increased demands driven by the changing economic environment and shifts in the way products and services are sold and delivered. These factors have created an imperative to leverage new and innovative technology solution architectures</p>
  <p class="abs strategy__link"><span>Read More</span></p>
</section>

<section>
  <span class="mark" style="left:592px;top:2680px"></span>
  <h2 class="abs section-title heading" style="top:2704px">Latest News</h2>

  <article class="abs news" style="left:162px;width:276px">
    <div class="news__photo" role="img" aria-label="Photo of audio and network rack equipment" style="background:linear-gradient(160deg,#3a4a8a,#d8a040 50%,#1a2340)"></div>
    <span class="news__date">4 August 2019</span>
    <h3 class="news__title">Lorem Ipsum is simply dummy text.</h3>
    <p class="news__text">Lorem Ipsum is simply dummy text of the printing and typesetting industry. Lorem Ipsum has been the industry's standard dummy text ever since the 1500s</p>
    <div class="news__more"><span>Read More</span></div>
  </article>
  <article class="abs news news--active" style="left:462px;width:272px">
    <div class="news__photo" role="img" aria-label="Photo of a hand holding a glowing digital world map" style="background:radial-gradient(circle at 50% 40%,#6fa8e8,#1c3e86 55%,#0b1a3c)"></div>
    <span class="news__date">4 August 2019</span>
    <h3 class="news__title">Lorem Ipsum is simply dummy text.</h3>
    <p class="news__text">Lorem Ipsum is simply dummy text of the printing and typesetting industry. Lorem Ipsum has been the industry's standard dummy text ever since the 1500s</p>
    <div class="news__more"><span>Read More</span></div>
  </article>
  <article class="abs news" style="left:760px;width:278px">
    <div class="news__photo" role="img" aria-label="Photo of colleagues working together at a laptop" style="background:linear-gradient(120deg,#e5e2df,#8a8f99 55%,#2e3442)"></div>
    <span class="news__date">4 August 2019</span>
    <h3 class="news__title">Lorem Ipsum is simply dummy text.</h3>
    <p class="news__text">Lorem Ipsum is simply dummy text of the printing and typesetting industry. Lorem Ipsum has been the industry's standard dummy text ever since the 1500s</p>
    <div class="news__more"><span>Read More</span></div>
  </article>
</section>

<section>
  <span class="mark" style="left:592px;top:3191px"></span>
  <h2 class="abs section-title heading" style="top:3214px">Contact Us</h2>
  <div class="abs field" style="left:162px;top:3300px;width:279px;height:44px">Name:</div>
  <div class="abs field" style="left:462px;top:3300px;width:278px;height:44px">Email:</div>
  <div class="abs field" style="left:759px;top:3300px;width:279px;height:44px">Phone:</div>
  <div class="abs field" style="left:162px;top:3361px;width:876px;height:87px">Message:</div>
  <a class="btn" style="left:533px;top:3502px;width:134px;height:36px">Drop Message</a>
</section>

<svg class="abs footer-bg" width="1200" height="400" viewBox="0 0 1200 400" aria-hidden="true">
  <polygon points="0,15 0,96 1200,30" fill="var(--pink)"/>
  <polygon points="0,96 1200,30 1200,400 0,400" fill="var(--dark)"/>
</svg>

<footer>
  <div class="abs footer__brand"><span class="brand__box"></span><span class="brand__name">Bork Ventures</span></div>
  <p class="abs footer__about">Bork Ventures, Inc. is an 8(a) full-service IT consulting company based in the Washington, DC Metro area. We offer specialized, highly customized technology.</p>
  <div class="abs social" aria-label="Social media links"><span></span><span></span><span></span><span></span></div>
  <div class="abs footer__col" style="left:387px"><h4>Quick Links</h4><ul><li>Home</li><li>About Us</li><li>Services</li><li>Strategy</li><li>IT News</li><li>Contact Us</li></ul></div>
  <div class="abs footer__col" style="left:532px"><h4>Strategy</h4><ul><li>Assess</li><li>Recommend</li><li>Implement</li><li>Monitor</li><li>Manage</li></ul></div>
  <div class="abs footer__col" style="left:658px"><h4>Services</h4><ul><li>Hardware / Software Sales</li><li>Professional Services</li><li>Technology Assessment</li><li>Technology Consulting</li></ul></div>
  <div class="abs footer__col" style="left:836px">
    <h4>Contact Info</h4>
    <div class="contact-row"><svg width="22" height="22" viewBox="0 0 24 24" aria-hidden="true"><path d="M6 3l4 4-2 3c1 2 3 4 6 6l3-2 4 4-3 3C10 21 3 14 3 6z" fill="var(--red)"/></svg><span>555-010-4821</span></div>
    <div class="contact-row"><svg width="22" height="22" viewBox="0 0 24 24" aria-hidden="true"><rect x="2" y="5" width="20" height="14" fill="var(--red)"/><path d="M2 5l10 8 10-8" fill="none" stroke="var(--dark)" stroke-width="1.5"/></svg><span>info@borkventuresinc.example</span></div>
    <div class="contact-row"><svg width="22" height="26" viewBox="0 0 24 28" aria-hidden="true"><path d="M12 1a9 9 0 0 1 9 9c0 7-9 17-9 17S3 17 3 10a9 9 0 0 1 9-9z" fill="var(--red)"/><circle cx="12" cy="10" r="3.5" fill="var(--dark)"/></svg><span>2200 Fernhollow Ct<br>Ashgrove, MD 20000</span></div>
  </div>
  <p class="abs copyright">© 2019 Bork Ventures, All Rights Reserved. Terms &amp; Conditions | Privacy Policy.</p>
</footer>

</body>
</html>
```